Corporate Business Card

Very professional, Modern, Not to busy, include phone address email, website
(253) 617-4930, 18761 52nd Avenue S, Kent, WA 98047, martin@plumlinegroup.com, varkoworks.com

Target Market(s)

Manufacturing

Industry/Entity Type

Aero, machining, manufacturing, Off road racing

Contact Information for Business Card

Phone, address email, website

```html
<!DOCTYPE html>
<html lang="en">
<head>
<meta charset="utf-8">
<title>Varko Works – Business Card</title>
<link rel="stylesheet" href="https://fonts.googleapis.com/css2?family=Exo+2:wght@700&family=Roboto:wght@400;700&display=swap">
<style>
  :root {
    --backdrop: #2b2b2b;
    --navy: #293766;
    --red: #c12026;
    --paper: #f2f2f2;
    --white: #ffffff;
  }
  * { box-sizing: border-box; margin: 0; padding: 0; }
  html, body { width: 1200px; height: 1138px; overflow: hidden; }
  body {
    background: var(--backdrop);
    font-family: "Roboto", Arial, sans-serif;
    position: relative;
  }
  .card {
    position: absolute;
    width: 620px;
    height: 375px;
    border-radius: 14px;
    overflow: hidden;
  }
  .card-front { left: 275px; top: 186px; background: var(--navy); }
  .card-back  { left: 276px; top: 608px; background: var(--paper); }

  .front-brand {
    position: absolute;
    left: 0; right: 0; top: 112px;
    text-align: center;
    color: var(--white);
    font-weight: 700;
    font-size: 64px;
    letter-spacing: 2px;
  }
  .front-rule {
    position: absolute;
    left: 105px; top: 211px;
    width: 470px; height: 2px;
    background: var(--white);
  }
  .front-web {
    position: absolute;
    left: 0; right: 0; top: 326px;
    text-align: center;
    color: var(--white);
    font-size: 16px;
    letter-spacing: 10px;
  }
  .front-web .accent { color: var(--red); }

  .back-brand {
    position: absolute;
    left: 52px; top: 68px;
    color: var(--navy);
    font-weight: 700;
    font-size: 36px;
    letter-spacing: 1px;
  }
  .back-rule {
    position: absolute;
    left: 48px; top: 137px;
    width: 250px; height: 2px;
    background: var(--navy);
  }
  .wave { position: absolute; inset: 0; width: 100%; height: 100%; }

  .holder {
    position: absolute;
    right: 28px; top: 196px;
    color: var(--white);
    font-family: "Exo 2", "Roboto", sans-serif;
    font-weight: 700;
    font-size: 25px;
    letter-spacing: 0.5px;
  }
  .contacts {
    position: absolute;
    right: 28px; top: 245px;
    list-style: none;
    color: var(--white);
    font-size: 16.5px;
    text-align: right;
  }
  .contacts li {
    display: flex;
    justify-content: flex-end;
    align-items: center;
    gap: 12px;
    height: 24px;
  }
  .contacts svg { width: 16px; height: 16px; fill: none; stroke: var(--white); stroke-width: 1.6; }
  .contacts .address { margin-top: 5px; height: 24px; }
</style>
</head>
<body>
  <section class="card card-front">
    <div class="front-brand">Varko Works</div>
    <div class="front-rule"></div>
    <p class="front-web">www.<span class="accent">varkoworks</span>.com</p>
  </section>

  <section class="card card-back">
    <div class="back-brand">Varko Works</div>
    <div class="back-rule"></div>

    <svg class="wave" viewBox="0 0 620 375" preserveAspectRatio="none" aria-hidden="true">
      <path fill="#c12026" d="M0,205 C120,272 230,270 340,205 C440,148 520,100 620,96 L620,375 L0,375 Z"/>
      <path fill="#f2f2f2" d="M0,232 C110,300 210,270 300,238 C210,282 110,290 0,250 Z"/>
      <path fill="#f2f2f2" d="M0,238 C115,296 230,285 340,224 C440,168 520,118 620,118 L620,375 L0,375 Z"/>
      <path fill="#293766" d="M0,248 C115,305 230,292 340,232 C440,176 520,122 620,128 L620,375 L0,375 Z"/>
    </svg>

    <h1 class="holder">MARTIN HALE</h1>
    <ul class="contacts">
      <li>(253) 617-4930
        <svg viewBox="0 0 16 16" aria-hidden="true"><path d="M2 5 C4 2 12 2 14 5 L12 7 L10 5.5 L6 5.5 L4 7 Z M4 8 L12 8 L13 13 L3 13 Z"/></svg>
      </li>
      <li>www.varkoworks.com
        <svg viewBox="0 0 16 16" aria-hidden="true"><circle cx="8" cy="8" r="6"/><path d="M2 8 H14 M8 2 C5 5 5 11 8 14 M8 2 C11 5 11 11 8 14"/></svg>
      </li>
      <li>martin@plumlinegroup.com
        <svg viewBox="0 0 16 16" aria-hidden="true"><rect x="2" y="4" width="12" height="8"/><path d="M2 4 L8 9 L14 4"/></svg>
      </li>
      <li class="address">18761 52nd Avenue S, Kent, WA 98047</li>
    </ul>
  </section>
</body>
</html>
```